Natural Supplement Co Needs Label Makeover

Our company's success began with our main product, an amino acid blend that aids in fat metabolism, called Vantorel. Since then we continue to expand the product line that now includes a detox called Vantopurge, and probiotic called Vantoflora, as well as 3 others, for a total of 6 products/ labels.
Our original design/logo had more of an 'old-timey' feel (see attached 2-product photo). We are looking for a fresh label design update for the product line which reflects the range of supplements as cohesive and individual parts of an overall health plan/strategy (see attached 'Logo Update Test' as just one idea we had in-house, you need not consider it as a starting point).

Target Market(s)

women 25-45

Industry/Entity Type

Health And Wellness

Requirements
Must have
• consistent theme with confident look
Nice to have
• Each product (ie. "Vantorel") has a few-word descriptor: ("Fat-Burning Amino Acids") that should be planned on including as part of each label.
Should not have
• NO 'streamlined' or graphic interpretations of the human body, or figurative image

```html
<!DOCTYPE html>
<html lang="en">
<head>
<meta charset="utf-8">
<title>Vantoflora and Vantorel Labels</title>
<link href="https://fonts.googleapis.com/css2?family=Quicksand:wght@400;500;600&display=swap" rel="stylesheet">
<style>
  :root {
    --page-bg: #efefef;
    --label-bg: #f1f1f0;
    --flora-green: #2f9a4a;
    --flora-tint: #dcebe0;
    --rorel-purple: #7a4c9c;
    --rorel-tint: #e7def0;
    --body-text: #5b5b5b;
  }
  * { margin: 0; padding: 0; box-sizing: border-box; }
  html, body { width: 1200px; height: 866px; overflow: hidden; }
  body {
    background: var(--page-bg);
    font-family: "Quicksand", sans-serif;
    position: relative;
  }
  .label {
    position: absolute;
    top: 190px;
    width: 300px;
    height: 480px;
    background: var(--label-bg);
    overflow: hidden;
    box-shadow: 0 2px 10px rgba(0,0,0,0.08);
  }
  .label--flora { left: 200px; --accent: var(--flora-green); --tint: var(--flora-tint); }
  .label--rorel { left: 700px; --accent: var(--rorel-purple); --tint: var(--rorel-tint); }

  .label__pattern {
    position: absolute;
    inset: 0;
    background:
      radial-gradient(ellipse 120% 40% at 30% 20%, var(--tint), transparent 70%),
      radial-gradient(ellipse 120% 35% at 70% 95%, var(--tint), transparent 70%);
  }
  .label__monogram {
    position: absolute;
    left: 22px;
    top: 0;
    width: 58px;
    height: 126px;
    background: var(--accent);
    color: #fff;
    font-weight: 500;
    font-size: 26px;
    display: flex;
    align-items: flex-end;
    justify-content: center;
    padding-bottom: 18px;
  }
  .label__name {
    position: absolute;
    left: 14px;
    top: 222px;
    color: var(--accent);
    font-size: 45px;
    line-height: 1;
    letter-spacing: 0.5px;
    white-space: nowrap;
  }
  .label--flora .label__name {
    font-weight: 400;
    font-size: 36px;
    top: 226px;
    left: 12px;
    padding-left: 8px;
    border-left: 2px solid var(--accent);
    letter-spacing: 0;
  }
  .label--rorel .label__name { font-weight: 600; }
  .label__name sup { font-size: 9px; vertical-align: top; margin-left: 2px; }
  .label__descriptor {
    position: absolute;
    left: 24px;
    top: 282px;
    color: var(--accent);
    font-size: 19px;
    font-weight: 500;
    padding-bottom: 4px;
    white-space: nowrap;
  }
  .label--rorel .label__descriptor { border-bottom: 2px solid var(--accent); font-weight: 600; }
  .label__body {
    position: absolute;
    left: 22px;
    right: 22px;
    top: 338px;
    color: var(--body-text);
    font-size: 8.6px;
    line-height: 1.45;
    text-align: justify;
  }
  .label__volume {
    position: absolute;
    left: 0; right: 0;
    bottom: 16px;
    text-align: center;
    color: var(--body-text);
    font-size: 13px;
    font-weight: 600;
  }
</style>
</head>
<body>
  <section class="label label--flora">
    <div class="label__pattern" role="img" aria-label="Soft green flowing line pattern"></div>
    <div class="label__monogram">VF</div>
    <h1 class="label__name">VANTOFLORA<sup>TM</sup></h1>
    <p class="label__descriptor">Fat-Burning Amino Acids</p>
    <p class="label__body">Lorem Ipsum is simply dummy text of the printing and typesetting industry. Lorem Ipsum has been the industry's standard dummy text ever since the 1500s, when an unknown printer took a galley of type and scrambled it to make a type specimen book. It has survived not only</p>
    <p class="label__volume">25 ML</p>
  </section>

  <section class="label label--rorel">
    <div class="label__pattern" role="img" aria-label="Soft purple flowing line pattern"></div>
    <div class="label__monogram">VR</div>
    <h1 class="label__name">VANTOREL<sup>TM</sup></h1>
    <p class="label__descriptor">Fat-Burning Amino Acids</p>
    <p class="label__body">Lorem Ipsum is simply dummy text of the printing and typesetting industry. Lorem Ipsum has been the industry's standard dummy text ever since the 1500s, when an unknown printer took a galley of type and scrambled it to make a type specimen book.</p>
    <p class="label__volume">25 ML</p>
  </section>
</body>
</html>
```